New Innovative Counselling and psychotherapy Service needs Business Card design

Keep it simple and professional. On one side, just company name and logo (perhaps in all blue) and maybe a tag line.

On other side (all white) my name and Qualifications in centre

Industry/Entity Type

Health And Wellness

Contact Information for Business Card

Dara Whelby
Counsellor & Psychotherapist
BSc (Psychol.), BA, Dip. (Couns. & Psych.), PG.Cert (CBT), FGTrK, ONRE

I will also require Mobile no, Email and web site address of which I'll pass on to final designer.

Font styles to use
Sans Serif

Requirements
Must have
• My Logo Only and please use the colours in logo that is in it.
Should not have
• Any other images

```html
<!DOCTYPE html>
<html lang="en">
<head>
<meta charset="utf-8">
<title>Brightwell Lane – Business Card</title>
<link rel="stylesheet" href="https://fonts.googleapis.com/css2?family=Roboto:wght@300;400;700&family=Roboto+Condensed:wght@700&display=swap">
<style>
  :root {
    --sky: #45b0ec;
    --sky-deep: #2f9fdf;
    --leaf: #8fd14f;
    --ink: #4a4a4a;
    --paper: #ffffff;
    --backdrop: #e9ebee;
  }
  * { box-sizing: border-box; margin: 0; padding: 0; }
  html, body {
    width: 1200px; height: 950px; overflow: hidden;
    background: var(--backdrop);
    font-family: "Roboto", Arial, sans-serif;
  }
  .sheet {
    position: relative; width: 1200px; height: 950px;
    display: flex; justify-content: center; align-items: center; gap: 60px;
  }
  .card {
    position: relative; width: 400px; height: 700px;
    border-radius: 4px; overflow: hidden;
    box-shadow: 0 6px 18px rgba(0,0,0,0.12);
  }

  /* Front: contact side */
  .card-front { background: var(--paper); text-align: center; padding-top: 70px; }
  .holder-name {
    font-family: "Roboto Condensed", "Roboto", sans-serif;
    font-weight: 700; font-size: 30px; color: var(--sky); letter-spacing: 0.5px;
  }
  .holder-role {
    font-family: "Roboto Condensed", "Roboto", sans-serif;
    font-weight: 700; font-size: 19px; color: var(--leaf); margin-top: 4px; letter-spacing: 0.4px;
  }
  .holder-quals { font-size: 14px; color: var(--leaf); line-height: 1.4; margin-top: 4px; }
  .holder-contact { font-size: 18px; color: var(--ink); line-height: 1.35; margin-top: 22px; }
  .front-brand {
    position: absolute; left: 0; right: 0; bottom: 150px;
    display: flex; flex-direction: column; align-items: center; gap: 26px;
  }
  .brand-dot { width: 150px; height: 150px; border-radius: 50%; background: var(--sky); }
  .brand-name-front { font-size: 36px; font-weight: 300; color: var(--sky); }

  /* Back: brand side */
  .card-back { background: var(--sky); }
  .back-lockup {
    position: absolute; left: 50%; top: 50%;
    width: 640px; transform: translate(-50%, -50%) rotate(90deg);
    display: flex; flex-direction: column; align-items: flex-start; padding-left: 40px;
  }
  .back-brand { display: flex; align-items: center; gap: 22px; }
  .brand-dot-small { width: 70px; height: 70px; border-radius: 50%; background: var(--paper); }
  .brand-name-back { font-size: 58px; font-weight: 300; color: var(--paper); }
  .tagline { font-size: 17px; color: var(--paper); margin-top: 14px; letter-spacing: 0.3px; }
</style>
</head>
<body>
<main class="sheet">
  <section class="card card-front" aria-label="Business card, contact side">
    <h1 class="holder-name">DARA WHELBY</h1>
    <p class="holder-role">COUNSELLOR &amp; PSYCHOTHERAPIST</p>
    <p class="holder-quals">BSc (Psychol.), BA, Dip. (Couns. &amp; Psych.)<br>PG.Cert (CBT), FGTrK.</p>
    <p class="holder-contact">(Ph) 812 507 3946<br>dara@Brightwelllane.com<br>www.Brightwelllane.com</p>
    <div class="front-brand">
      <span class="brand-dot"></span>
      <span class="brand-name-front">Brightwell Lane</span>
    </div>
  </section>

  <section class="card card-back" aria-label="Business card, brand side">
    <div class="back-lockup">
      <div class="back-brand">
        <span class="brand-dot-small"></span>
        <span class="brand-name-back">Brightwell Lane</span>
      </div>
      <p class="tagline">Your Psychological Well-Being Is Our Top Priority</p>
    </div>
  </section>
</main>
</body>
</html>
```